Home Staging Company needs business card design

We're a home staging company called Brightly Settled Home Staging. We would like a business card design that includes aqua and gray. Our current logo of house within chair is fine but I find we almost always use the logo in one color. I'll upload images of front and back of our current card and our logo. Note that we have dropped "Solutions" from our company name and don't want to include it on the card.

Target Market(s)

Realtors and homeowners - people interested in selling their homes

Contact Information for Business Card

Marisol Thistlewood
Brightly Settled Home Staging
757-555-0193
www.brightlysettled.com
marisol@brightlysettled.com

Font styles to use
Serif
Script

Requirements
Must have
• My logo and contact details
• UPDATE***
• I forgot to say that the company name should be included on the front of the card somehow.

```html
<!DOCTYPE html>
<html lang="en">
<head>
<meta charset="utf-8">
<title>Brightly Settled Home Staging – Business Card</title>
<link rel="stylesheet" href="https://fonts.googleapis.com/css2?family=Playfair+Display:wght@400&family=Roboto:wght@400&family=Open+Sans:wght@400&display=swap">
<style>
  :root {
    --backdrop: #b4b4b4;
    --card-dark: #373b3e;
    --mark-faint: #3f4447;
    --card-light: #f4f4f3;
    --ink: #2e3235;
    --ink-soft: #4a4e52;
    --aqua: #4faab5;
    --aqua-light: #62b9c4;
    --white: #f2f2f2;
  }
  * { margin: 0; padding: 0; box-sizing: border-box; }
  html, body { width: 1200px; height: 576px; overflow: hidden; }
  body { background: var(--backdrop); position: relative; }

  .card {
    position: absolute;
    width: 484px;
    height: 293px;
    border-radius: 14px;
    overflow: hidden;
  }
  .card--back { left: 82px; top: 138px; background: var(--card-dark); }
  .card--front { left: 602px; top: 138px; background: var(--card-light); }

  .mark-area { position: absolute; display: block; }
  .card--back .mark-area { left: 92px; top: -20px; width: 300px; height: 300px; }
  .card--front .mark-area { left: 262px; top: 20px; width: 260px; height: 260px; }

  .company-name {
    position: absolute;
    font-family: "Playfair Display", serif;
    font-weight: 400;
    line-height: 1.05;
  }
  .card--back .company-name {
    left: 0; right: 0; top: 104px;
    text-align: center;
    color: var(--white);
    font-size: 38px;
  }
  .card--back .website {
    position: absolute;
    left: 0; right: 0; bottom: 14px;
    text-align: center;
    font-family: "Open Sans", sans-serif;
    font-size: 13.5px;
    color: var(--aqua-light);
  }

  .card--front .company-name {
    left: 22px; top: 34px;
    color: var(--ink);
    font-size: 26px;
  }

  .person { position: absolute; left: 22px; top: 164px; }
  .person__name {
    font-family: "Roboto", sans-serif;
    font-size: 18.5px;
    color: var(--ink);
    letter-spacing: 0.2px;
  }
  .person__surname { color: var(--aqua); }
  .person__title {
    margin-top: 3px;
    font-family: "Open Sans", sans-serif;
    font-size: 11.5px;
    color: var(--ink-soft);
  }

  .contacts {
    position: absolute;
    left: 28px; top: 219px;
    list-style: none;
    font-family: "Open Sans", sans-serif;
    font-size: 12.2px;
    color: var(--ink);
  }
  .contacts li { display: flex; align-items: center; height: 17px; }
  .contacts svg { width: 11px; height: 11px; margin-right: 9px; fill: none; stroke: var(--aqua); stroke-width: 1.6; }
  .contacts svg .solid { fill: var(--aqua); stroke: none; }
</style>
</head>
<body>
  <section class="card card--back" aria-label="Card back">
    <svg class="mark-area" viewBox="0 0 300 300" role="img" aria-label="Faint company mark area">
      <circle cx="150" cy="150" r="150" fill="var(--mark-faint)"/>
    </svg>
    <h1 class="company-name">Brightly Settled<br>Home Staging</h1>
    <p class="website">www.brightlysettled.com</p>
  </section>

  <section class="card card--front" aria-label="Card front">
    <svg class="mark-area" viewBox="0 0 260 260" role="img" aria-label="Company mark area">
      <circle cx="130" cy="130" r="130" fill="var(--aqua)"/>
    </svg>
    <h2 class="company-name">Brightly Settled<br>Home Staging</h2>

    <div class="person">
      <p class="person__name">Marisol <span class="person__surname">Thistlewood</span></p>
      <p class="person__title">Managing Director</p>
    </div>

    <ul class="contacts">
      <li>
        <svg viewBox="0 0 12 12" aria-hidden="true"><path class="solid" d="M1 4.5C1 2.5 3 1.5 6 1.5S11 2.5 11 4.5L9 5 8.5 3.8h-5L3 5zM2.5 6.5h7l1 4h-9z"/></svg>
        757-555-0193
      </li>
      <li>
        <svg viewBox="0 0 12 12" aria-hidden="true"><circle cx="6" cy="6" r="4.8"/><path d="M1.2 6h9.6M6 1.2c-2.4 2.8-2.4 6.8 0 9.6M6 1.2c2.4 2.8 2.4 6.8 0 9.6"/></svg>
        www.brightlysettled.com
      </li>
      <li>
        <svg viewBox="0 0 12 12" aria-hidden="true"><path class="solid" d="M0.5 2.5h11v7h-11z"/><path d="M0.8 2.8 6 6.8l5.2-4" stroke="var(--card-light)" stroke-width="1.1"/></svg>
        marisol@brightlysettled.com
      </li>
    </ul>
  </section>
</body>
</html>
```